Business Card Design for company

We want new business cards. We'd like something different-- yet still highly professional. Our tagline is Providing leadership, delivering success. Stock photos are ok, as long as they are relevant and look upscale.

Target Market(s)

Architecture/Business Management Consulting/Engineering Consulting

Contact Information for Business Card

dark gray background with pops of blue might be good, but you tell me. You're the designers. Rounded corners might be nice, but again, you tell me.

Font styles to use
Serif
Sans Serif

Colors
3276b5
5c5c5c
9d9d9d
fbfbfb

Requirements
Nice to have
• Something different, but still very professional.

```html
<!DOCTYPE html>
<html lang="en">
<head>
<meta charset="utf-8">
<title>Norvale Partners – Business Cards</title>
<link href="https://fonts.googleapis.com/css2?family=Montserrat:wght@500;600;700&family=Open+Sans:wght@400;600&display=swap" rel="stylesheet">
<style>
  :root {
    --brand-blue: #3276b5;
    --charcoal: #333333;
    --slate: #5c5c5c;
    --silver: #9d9d9d;
    --paper: #fbfbfb;
    --backdrop: #d9d9d9;
    --rule: #e4e4e4;
  }
  * { margin: 0; padding: 0; box-sizing: border-box; }
  html, body {
    width: 1200px; height: 900px; overflow: hidden;
    background: var(--backdrop);
  }
  .stage { position: relative; width: 1200px; height: 900px; }

  .card {
    position: absolute;
    width: 560px; height: 320px;
    border-radius: 26px;
    box-shadow: 0 10px 24px rgba(0,0,0,0.18);
    overflow: hidden;
  }

  /* Back of card */
  .card--back {
    left: 90px; top: 110px;
    background: var(--charcoal);
    display: flex; flex-direction: column; align-items: center; justify-content: center;
  }
  .wordmark {
    font-family: "Montserrat", sans-serif;
    font-weight: 700;
    color: var(--brand-blue);
    letter-spacing: 1px;
    text-transform: uppercase;
    white-space: nowrap;
  }
  .card--back .wordmark { font-size: 40px; }
  .tagline {
    margin-top: 70px;
    font-family: "Montserrat", sans-serif;
    font-weight: 600;
    font-size: 15px;
    letter-spacing: 0.6px;
    color: var(--paper);
    text-transform: uppercase;
  }

  /* Front of card */
  .card--front {
    left: 550px; top: 470px;
    background: var(--paper);
  }
  .card--front .wordmark {
    position: absolute; right: 36px; top: 44px;
    font-size: 34px;
  }
  .divider {
    position: absolute; left: 36px; right: 36px; top: 128px;
    height: 1px; background: var(--rule);
  }
  .contact {
    position: absolute; left: 36px; bottom: 30px;
    font-family: "Open Sans", sans-serif;
    color: var(--slate);
  }
  .contact__name {
    font-family: "Montserrat", sans-serif;
    font-weight: 700;
    font-size: 21px;
    text-transform: uppercase;
    letter-spacing: 0.4px;
  }
  .contact__name .first { color: var(--brand-blue); }
  .contact__name .last { color: var(--slate); }
  .contact__role { font-size: 15px; margin-bottom: 6px; }
  .contact__list { list-style: none; }
  .contact__list li {
    display: flex; align-items: center; gap: 8px;
    font-size: 15px; line-height: 21px;
  }
  .contact__list svg { width: 12px; height: 12px; flex: none; }
  .address {
    position: absolute; right: 36px; top: 158px;
    text-align: right;
    font-family: "Open Sans", sans-serif;
    font-size: 14px; line-height: 20px;
    color: var(--slate);
  }
</style>
</head>
<body>
<main class="stage">

  <section class="card card--back" aria-label="Card back">
    <div class="wordmark">Norvale Partners</div>
    <p class="tagline">Providing leadership, delivering success</p>
  </section>

  <section class="card card--front" aria-label="Card front">
    <div class="wordmark">Norvale Partners</div>
    <div class="divider"></div>

    <address class="address" style="font-style:normal">
      12345, Address Goes Here<br>
      Country Name, 123456
    </address>

    <div class="contact">
      <div class="contact__name"><span class="first">Adrian</span> <span class="last">Cole</span></div>
      <div class="contact__role">Managing Director</div>
      <ul class="contact__list">
        <li>
          <svg viewBox="0 0 12 12" aria-hidden="true"><path fill="#3276b5" d="M1 4c0-2 2-3 5-3s5 1 5 3l-2 1-1-2H4L3 5 1 4zm2 2h6l1 5H2l1-5zm3 1.2a1.4 1.4 0 1 0 0 2.8 1.4 1.4 0 0 0 0-2.8z"/></svg>
          044-123 456 789
        </li>
        <li>
          <svg viewBox="0 0 12 12" aria-hidden="true"><rect x="3" y="0.5" width="6" height="11" rx="1" fill="none" stroke="#3276b5" stroke-width="1.2"/><circle cx="6" cy="9.5" r="0.7" fill="#3276b5"/></svg>
          044-123 456 789
        </li>
        <li>
          <svg viewBox="0 0 12 12" aria-hidden="true"><rect x="0.5" y="2" width="11" height="8" fill="#3276b5"/><path d="M0.5 2 6 6.5 11.5 2" fill="none" stroke="#fbfbfb" stroke-width="1"/></svg>
          info@norvalepartners.com
        </li>
        <li>
          <svg viewBox="0 0 12 12" aria-hidden="true"><circle cx="6" cy="6" r="5.5" fill="#3276b5"/><path d="M0.5 6h11M6 0.5c-2.5 3-2.5 8 0 11M6 0.5c2.5 3 2.5 8 0 11" fill="none" stroke="#fbfbfb" stroke-width="0.8"/></svg>
          www.norvalepartners.com
        </li>
      </ul>
    </div>
  </section>

</main>
</body>
</html>
```